KLV Plant Services

We are a heavy diesel mechanical business with additional air con certificates, remapping engine rebuilt

Contact Information for Business Card

Company Name, Director Name, Managing Director, Contact details, email and website

Font styles to use
Serif
Script

```html
<!DOCTYPE html>
<html lang="en">
<head>
<meta charset="utf-8">
<title>KLV Plant Services – Business Card</title>
<link href="https://fonts.googleapis.com/css2?family=Montserrat:wght@600;700&family=Questrial&display=swap" rel="stylesheet">
<style>
  :root {
    --navy-deep: #07063a;
    --navy-mid: #1b1668;
    --brand-blue: #262083;
    --ink: #3a3a44;
    --card-white: #fbfbfb;
    --card-grey: #e9e9ec;
    --stage: #d9d6d1;
    --rule: #b9b9c0;
  }
  * { box-sizing: border-box; margin: 0; padding: 0; }
  html, body { width: 1200px; height: 900px; overflow: hidden; }
  body {
    background: var(--stage);
    display: flex;
    flex-direction: column;
    align-items: center;
    justify-content: center;
    gap: 48px;
    font-family: "Questrial", "Helvetica Neue", Arial, sans-serif;
  }
  .card {
    width: 620px;
    height: 354px;
    border-radius: 28px;
    position: relative;
    overflow: hidden;
    box-shadow: 0 10px 24px rgba(0,0,0,0.25);
  }
  .card-front {
    background: radial-gradient(ellipse at 50% 45%, var(--navy-mid) 0%, var(--navy-deep) 75%);
    display: flex;
    align-items: center;
    justify-content: center;
  }
  .brand {
    display: flex;
    align-items: center;
    gap: 14px;
    font-family: "Montserrat", Arial, sans-serif;
    font-weight: 700;
    font-size: 34px;
    letter-spacing: 0.5px;
  }
  .brand-dot {
    width: 22px; height: 22px; border-radius: 50%;
  }
  .card-front .brand { color: #ffffff; }
  .card-front .brand-dot { border: 3px solid #ffffff; }
  .card-back {
    background: linear-gradient(120deg, var(--card-grey) 0%, var(--card-white) 55%, var(--card-grey) 100%);
    display: flex;
    align-items: center;
  }
  .card-back .brand-area {
    width: 290px;
    display: flex;
    justify-content: center;
  }
  .card-back .brand { color: var(--brand-blue); font-size: 24px; gap: 10px; }
  .card-back .brand-dot { width: 16px; height: 16px; border: 3px solid var(--brand-blue); }
  .divider {
    width: 1px;
    height: 230px;
    background: linear-gradient(to bottom, transparent, var(--rule) 20%, var(--rule) 80%, transparent);
  }
  .contact {
    padding-left: 34px;
    color: var(--ink);
  }
  .person-name {
    font-family: "Montserrat", Arial, sans-serif;
    font-weight: 700;
    font-size: 20px;
    color: var(--brand-blue);
    letter-spacing: 0.5px;
  }
  .person-role { font-size: 15px; margin-top: 2px; }
  .details { list-style: none; margin-top: 26px; font-size: 14.5px; line-height: 1.55; }
  .details li { display: flex; align-items: flex-start; gap: 10px; }
  .details svg { width: 14px; height: 14px; margin-top: 4px; flex: none; fill: var(--brand-blue); }
</style>
</head>
<body>
  <section class="card card-front">
    <div class="brand"><span class="brand-dot"></span>KLV Plant Services</div>
  </section>

  <section class="card card-back">
    <div class="brand-area">
      <div class="brand"><span class="brand-dot"></span>KLV Plant Services</div>
    </div>
    <div class="divider"></div>
    <div class="contact">
      <p class="person-name">DANIEL HART</p>
      <p class="person-role">Managing Director</p>
      <ul class="details">
        <li><svg viewBox="0 0 24 24"><path d="M6.6 10.8a15.1 15.1 0 0 0 6.6 6.6l2.2-2.2c.3-.3.7-.4 1-.2 1.1.4 2.3.6 3.6.6.6 0 1 .4 1 1V20c0 .6-.4 1-1 1A17 17 0 0 1 3 4c0-.6.4-1 1-1h3.5c.6 0 1 .4 1 1 0 1.3.2 2.5.6 3.6.1.3 0 .7-.2 1z"/></svg>0400 152 936</li>
        <li><svg viewBox="0 0 24 24"><path d="M2 5h20v14H2z M2 5l10 8 10-8" fill="none" stroke="#262083" stroke-width="2.4"/></svg>admin@klvplantservices.net</li>
        <li><svg viewBox="0 0 24 24"><g fill="none" stroke="#262083" stroke-width="2"><circle cx="12" cy="12" r="10"/><ellipse cx="12" cy="12" rx="4.5" ry="10"/><path d="M2 12h20M4 7h16M4 17h16"/></g></svg>www.klvplantservices.net</li>
        <li><svg viewBox="0 0 24 24"><path d="M12 2a7 7 0 0 0-7 7c0 5.3 7 13 7 13s7-7.7 7-13a7 7 0 0 0-7-7zm0 9.5A2.5 2.5 0 1 1 12 6.5a2.5 2.5 0 0 1 0 5z"/></svg><span>48 Ridge Road, Westfield<br>WA 6000, Australia</span></li>
      </ul>
    </div>
  </section>
</body>
</html>
```